American cannabis tech company business card design

Pavrel.com is seeking a modern, professional, and brand-aligned business card that represents our company and its core values: Mission, Story, Values, and Impact. As an innovative cannabis company, we want a business card that is not only visually appealing but also serves as a representation of who we are and what we stand for.

Project Scope: Design a double-sided business card that integrates our brand identity and core values. Incorporate our key brand elements, ensuring a sleek and contemporary aesthetic. Visually reflect our core values (Mission, Story, Values, Impact) in a way that is engaging yet professional.

Target Market(s)

Vendors, third parties,

Contact Information for Business Card

Contact details (name, title, email, phone, website, etc.)

Font styles to use
Other font styles liked:
• Caslon, Centra

Colors

Designer to choose colors to be used in the design.

Requirements
Must have
• Pavrel.com logo and branding A creative yet clean way to integrate our core values (Mission, Story, Values, Impact) Modern typography and a well-structured layout
Nice to have
• forest green, grey, white, black
Should not have
• references to marijuana, leafs, plants, or related product

```html
<!DOCTYPE html>
<html lang="en">
<head>
<meta charset="utf-8">
<title>Pavrel.com Business Card</title>
<link href="https://fonts.googleapis.com/css2?family=Montserrat:wght@400;500;700;800&display=swap" rel="stylesheet">
<style>
  :root {
    --forest: #1a3120;
    --paper: #ffffff;
    --ink: #1c1c1c;
    --stage: #e9ebe8;
  }
  * { margin: 0; padding: 0; box-sizing: border-box; }
  html, body { width: 1200px; height: 900px; overflow: hidden; }
  body {
    background: var(--stage);
    font-family: "Montserrat", sans-serif;
    position: relative;
  }
  .card {
    position: absolute;
    left: 280px;
    width: 640px;
    height: 366px;
    border-radius: 22px;
    box-shadow: 0 6px 20px rgba(0,0,0,0.12);
  }
  .card-front {
    top: 58px;
    background: var(--forest);
    display: flex;
    align-items: center;
    justify-content: center;
  }
  .card-front .wordmark {
    color: var(--paper);
    font-size: 104px;
    font-weight: 800;
    letter-spacing: 1px;
  }
  .card-back {
    top: 476px;
    background: var(--paper);
  }
  .card-back .wordmark {
    position: absolute;
    left: 44px;
    top: 118px;
    color: var(--forest);
    font-size: 62px;
    font-weight: 800;
    letter-spacing: 0.5px;
  }
  .divider {
    position: absolute;
    left: 368px;
    top: 98px;
    width: 2px;
    height: 128px;
    background: var(--forest);
  }
  .contact {
    position: absolute;
    left: 392px;
    top: 100px;
    color: var(--forest);
  }
  .contact .name { font-size: 24px; font-weight: 700; line-height: 1.05; }
  .contact .title { font-size: 14px; font-weight: 500; color: #3d4a40; margin-bottom: 10px; }
  .contact ul { list-style: none; }
  .contact li {
    display: flex; align-items: center; gap: 8px;
    font-size: 15px; font-weight: 500; color: var(--ink); line-height: 1.4;
  }
  .contact svg { width: 12px; height: 12px; fill: var(--ink); flex: none; }
  .address {
    position: absolute;
    left: 0; right: 0;
    top: 282px;
    text-align: center;
    font-size: 15px;
    color: var(--ink);
    padding-right: 60px;
  }
</style>
</head>
<body>
  <section class="card card-front">
    <span class="wordmark">PAVREL</span>
  </section>

  <section class="card card-back">
    <span class="wordmark">PAVREL</span>
    <div class="divider"></div>
    <div class="contact">
      <div class="name">Marcus Hale</div>
      <div class="title">Co-Founder &amp; CEO</div>
      <ul>
        <li>
          <svg viewBox="0 0 12 12"><path d="M2.5 1h2l1 3-1.5 1a7 7 0 0 0 3 3l1-1.5 3 1v2a1 1 0 0 1-1 1A10 10 0 0 1 1.5 2a1 1 0 0 1 1-1z"/></svg>
          +1 405-555-0148
        </li>
        <li>
          <svg viewBox="0 0 12 12"><path d="M0 2.5h12v7H0z M0 2.5l6 4 6-4" stroke="#fff" stroke-width="0.8"/></svg>
          team@pavrel.com
        </li>
        <li>
          <svg viewBox="0 0 12 12"><circle cx="6" cy="6" r="5.5"/><path d="M0.5 6h11M6 0.5c-2.5 3-2.5 8 0 11M6 0.5c2.5 3 2.5 8 0 11" stroke="#fff" stroke-width="0.7" fill="none"/></svg>
          www.pavrel.com
        </li>
      </ul>
    </div>
    <div class="address">1187 Birch Avenue, Dallas, TX 75204</div>
  </section>
</body>
</html>
```